Web Design Project for a Software & Consulting Company

We have just completed a recent ArtHerdly project for a new logo (see attached).
As the next stage of our rebranding we now require a website re-design to complement the new logo.
Our current site, http://www.corvinsoft.example was built in-house and does not come across as professional as we would like. We supply software and associated services to some of the world’s largest oil companies and we need our site to reflect that level of client.
We will also be posting another design project for brochures, PowerPoint slides and other materials very soon.
We would like designs for…
Home page
Product page
• TZQ
• BLV
• PNJ
Services
News page
About Us page
Contact Us page
Page for mobile devices that gives basic company and product information
Currently the site is small but we intend to increase content to include white papers etc. this should be taken into account when designing the navigation therefore we would prefer navigation through styled text links rather than images.
Colour schemes should broadly be taken from our new logo, where the dark blue and dark green from the left and right sides of the logo are the main colours, but other, brighter accent colours can be used to highlight sections or content.
Dark Blue = C:88, M:55, Y:44, K:28
Dark Green = C:87, M:53, Y:50, K:50
NB: Don’t use the logo on our current site, make sure you use the one attached.
We would prefer the final file format to be a layered PSD.
The site should be clean and professional and communicate the following...
• That we have a great depth and breadth of knowledge about our customers’ business, enabling us to deliver the best systems and solutions.
• That we are a leading provider of cost estimation and control solutions to the oil and gas industry.
• The benefits of our software and consulting services.
• Show that we deliver outstanding customer service and value with a very high level of professionalism
• The site should have no Flash and be able to self-adjust to fit any screen size.
Things to avoid …
• Obvious and clichéd oil industry imagery, no oil rigs
• Cartoon style graphics
Our Background
We are an integrated software and consulting organization specialising in the drilling side of the oil and gas industry. Simply put our software helps companies better understand, predict and communicate the cost of drilling wells.
We have 3 software products and a consulting offering consisting of…
• TZQ - Probabilistic time and cost software
• BLV – Cost tracking and reporting software
• PNJ – (currently known as DrillSavant) – Lessons learned software
• Consulting services
Our systems are in use in over 30 countries with a broad range of clients including: GN, Marovel, Dunt, Koruna, VELO Sirkami, FALUMI and Quintex.
Our current site can be found at www.corvinsoft.example
Our main competitors are
• http://www.drovanic.example/
• http://www.sumbrask.example/
• http://www.kve.example/services/software-solutions/p1-
Our depth of drilling knowledge, quality of software and collaboration with clients differentiate us form the competition.
We strive for very high levels of customer service.
We look forward to receiving your designs!
Updates
Thanks to all the designers who have submitted a design, we appreciate the effort.
We will do our best to give individual feedback on each design but given that many are quite similar we thought we would give some general feedback first.
Nearly all the designs submitted so far have been slight variations on…
-
Top Menu
-
Scrolling Photo Banner
-
4 Columns
-
Body
-
Deep Footer
These designs are well executed but they are basically the same layout as our existing site and while there is nothing inherently wrong with this layout we would like to see some designs that are a bit more innovative and different. We don’t really want just a polished version of our current site.
Thanks again,
CVS
Thanks to everyone who has submitted a design, the response has been great.
We are close to making a decision so if you are intending to submit a design please do it soon, the deadline is only a few days away.
Thanks again.
CVS
Target Market(s)
Mid to high level executives
Industry/Entity Type
Oil And Gas
Look and feel

```html
<!DOCTYPE html>
<html lang="en">
<head>
<meta charset="utf-8">
<title>Corvin Software</title>
<link href="https://fonts.googleapis.com/css2?family=Archivo+Black&family=PT+Sans:wght@400;700&family=Arimo:wght@400;700&display=swap" rel="stylesheet">
<style>
:root{
  --teal:#4f8790;
  --teal-dark:#1f5060;
  --ink:#0f3d4c;
  --text:#555;
  --light:#ebebeb;
  --line:#d4d4d4;
  --white:#fff;
}
*{margin:0;padding:0;box-sizing:border-box}
html,body{width:1200px;height:892px;overflow:hidden;background:var(--white)}
.page{position:absolute;left:0;top:0;width:1400px;height:1041px;transform:scale(.857143);transform-origin:0 0;font-family:"Arimo",Arial,sans-serif}
.abs{position:absolute}
.top-band{left:210px;top:0;width:980px;height:11px;background:var(--teal);border-radius:0 0 6px 6px}
.brand{left:212px;top:30px;display:flex;align-items:center;gap:12px}
.brand-mark{width:60px;height:60px;border-radius:50%;background:var(--teal)}
.brand-name{font-family:"PT Sans",sans-serif;font-weight:700;font-size:30px;color:var(--teal-dark);letter-spacing:1px;line-height:1}
.nav a{position:absolute;top:88px;font-family:"PT Sans",sans-serif;font-size:13px;color:var(--ink);text-decoration:none;white-space:nowrap}
.hero{left:210px;top:139px;width:980px;height:367px;border-radius:8px;overflow:hidden;background:linear-gradient(90deg,#dfe8ee 0%,#eef2f4 35%,#d9d4cf 60%,#b89a84 80%,#8b6f5c 100%)}
.hero-title{left:248px;top:283px;font-family:"Archivo Black",sans-serif;font-size:44px;color:var(--teal);letter-spacing:.5px}
.hero-sub{left:248px;top:335px;font-family:"PT Sans",sans-serif;font-size:24px;line-height:34px;color:#3a3a3a}
.dots{left:1112px;top:479px;display:flex;gap:2px}
.dots span{width:11px;height:11px;border-radius:50%;background:var(--white)}
.dots span:first-child{background:var(--teal)}
.dropdown{left:704px;top:117px;width:124px;height:102px;background:#f6f6f6;border:1px solid #dcdcdc;border-radius:6px;box-shadow:0 2px 6px rgba(0,0,0,.12);padding:12px 10px 0 21px;font-family:"PT Sans",sans-serif;font-size:12px;color:#444}
.dropdown li{list-style:none;height:28px;line-height:24px;border-bottom:1px solid #ddd}
.dropdown li:last-child{border:0}
.pillar-head{top:527px;font-family:"Archivo Black",sans-serif;font-size:21px;color:var(--teal-dark)}
.pillars{left:210px;top:560px;width:981px;height:151px}
.pillar{top:583px;width:205px}
.pillar h3{font-weight:400;font-size:17px;color:var(--ink);margin-bottom:14px;white-space:nowrap}
.pillar p{font-size:11px;line-height:18px;color:var(--text)}
.pillar.active h3,.pillar.active p{color:var(--white)}
.clients-head{left:210px;top:728px;font-family:"Archivo Black",sans-serif;font-size:21px;color:var(--teal-dark)}
.clients{left:210px;top:768px;display:flex;gap:10px}
.client{width:100px;height:67px;border:1px solid var(--line);border-radius:3px;display:flex;align-items:center;justify-content:center;font-weight:700;font-size:15px;color:var(--teal-dark)}
.foot-band{left:210px;top:866px;width:980px;height:11px;background:var(--teal);border-radius:6px 6px 0 0}
.region{top:895px;font-size:14px;color:#999}
.card{top:918px;height:99px;border:1px solid var(--line);border-radius:8px;padding:10px 4px 10px 20px;font-size:11px;line-height:18px;color:var(--ink);white-space:nowrap}
.card .row{display:flex;align-items:center;gap:3px;margin-top:3px}
.partner{left:658px;top:905px;display:flex;align-items:center;gap:12px}
.partner-badge{width:40px;height:40px;background:var(--teal);border-radius:6px}
.partner-name{font-family:"PT Sans",sans-serif;font-size:22px;font-weight:700;color:#222}
.partner-sub{font-family:"PT Sans",sans-serif;font-size:12px;color:#333}
.social{left:994px;top:903px;font-size:11px;line-height:15px;color:var(--ink);text-align:right;display:flex;gap:9px;align-items:center}
.social i{display:inline-block;width:24px;height:24px;border-radius:50%;background:#8a9aa2}
.copy{left:1060px;top:954px;width:129px;text-align:right;font-size:9.5px;line-height:15px;color:#888}
.copy b{color:var(--ink);font-weight:400}
</style>
</head>
<body>
<div class="page">
  <div class="abs top-band"></div>
  <div class="abs brand"><span class="brand-mark"></span><span class="brand-name">CORVIN SOFTWARE</span></div>
  <nav class="nav">
    <a href="#" style="left:616px">Home</a><a href="#" style="left:709px">Products</a><a href="#" style="left:817px">Services</a>
    <a href="#" style="left:920px">News</a><a href="#" style="left:1010px">About us</a><a href="#" style="left:1118px">Contact us</a>
  </nav>

  <div class="abs hero" role="img" aria-label="Banner photo: smiling businesswoman in front of pale industrial equipment"></div>
  <div class="abs hero-title">We develop software</div>
  <div class="abs hero-sub">and associated services to some of the<br>world’s largest oil companies</div>
  <div class="abs dots"><span></span><span></span><span></span><span></span><span></span></div>
  <ul class="abs dropdown"><li>TZQ</li><li>BLV</li><li>PNJ</li></ul>

  <div class="abs pillar-head" style="left:210px">Plan</div>
  <div class="abs pillar-head" style="left:490px">Execute</div>
  <div class="abs pillar-head" style="left:739px">Learn</div>
  <div class="abs pillar-head" style="left:983px">Embed</div>
  <svg class="abs pillars" viewBox="0 0 981 151">
    <rect width="981" height="151" rx="3" fill="var(--light)"/>
    <polygon points="0,0 248,0 265,75 248,151 0,151" fill="var(--teal-dark)"/>
    <polyline points="250,0 267,75 250,151" fill="none" stroke="#fff" stroke-width="4"/>
    <polyline points="498,0 514,75 498,151" fill="none" stroke="#fff" stroke-width="4"/>
    <polyline points="747,0 763,75 747,151" fill="none" stroke="#fff" stroke-width="4"/>
  </svg>
  <div class="abs pillar active" style="left:233px"><h3>Time &amp; Cost Estimation</h3><p style="padding-left:3px">TZQ delivers a standardized, systematic approach to understanding, quantifying and communicating the impact of project risk to all stakeholders.</p></div>
  <div class="abs pillar" style="left:492px"><h3>Materials &amp; Cost Control</h3><p>Since 1992 BLV has been helping companies optimize their materials and logistics processes and accurately track costs on a daily basis.</p></div>
  <div class="abs pillar" style="left:740px"><h3>Lessons Learned</h3><p>DrillSavant is an advanced lessons learned and knowledge management system for use in the Oil &amp; Gas industry. It's fully searchable and easy to use.</p></div>
  <div class="abs pillar" style="left:987px;width:192px"><h3>Services &amp; Consulting</h3><p>Software solutions rely on people and processes to deliver results. From analysis through execution we support our clients to improve performance</p></div>

  <div class="abs clients-head">Clients</div>
  <div class="abs clients">
    <div class="client">Dunt</div><div class="client">Marovel</div><div class="client">VELO</div>
    <div class="client">FALUMI</div><div class="client">Baltor</div><div class="client">Kessrand</div>
    <div class="client">Orrin</div><div class="client">Koruna</div><div class="client">GN</div>
  </div>

  <div class="abs foot-band"></div>
  <div class="abs region" style="left:211px">EUROPE</div>
  <div class="abs region" style="left:411px">NORTH AMERICA</div>
  <div class="abs card" style="left:210px;width:179px">12 HARLOW LANE<br>KINROSS, KR4 2PL
    <div class="row"><svg width="18" height="14" viewBox="0 0 18 14"><rect x="1" y="1" width="5" height="12" rx="1" fill="#9aa"/><rect x="7" y="3" width="10" height="10" fill="#bbb"/></svg>: +44(0)1000 555012</div>
    <div class="row"><svg width="18" height="12" viewBox="0 0 18 12"><rect x="1" y="1" width="16" height="10" fill="#bbb"/><polyline points="1,1 9,7 17,1" fill="none" stroke="#fff"/></svg>: eu@corvinsoft.example</div></div>
  <div class="abs card" style="left:410px;width:219px">4100 MERIDIAN BLVD, SUITE 210<br>DALTON, TX 75001
    <div class="row"><svg width="18" height="14" viewBox="0 0 18 14"><rect x="1" y="1" width="5" height="12" rx="1" fill="#9aa"/><rect x="7" y="3" width="10" height="10" fill="#bbb"/></svg>: (555) 014 2278</div>
    <div class="row"><svg width="18" height="12" viewBox="0 0 18 12"><rect x="1" y="1" width="16" height="10" fill="#bbb"/><polyline points="1,1 9,7 17,1" fill="none" stroke="#fff"/></svg>: us@corvinsoft.example</div></div>
  <div class="abs partner"><span class="partner-badge"></span><div><div class="partner-name">Vantrel Partner</div><div class="partner-sub">Gold Enterprise Resource Planning</div></div></div>
  <div class="abs social"><span>Connect to<br>our Social Network :</span><i></i><i></i><i></i></div>
  <div class="abs copy">© 2013 <b>Corvin Software</b>.<br>All rights reserved.</div>
</div>
</body>
</html>
```